Business Card and Letterhead for Pimlu - modern real estate business

I need a double sided business card design for Pimlu. Please see business card brief here https://files.trelvonadocs.com/sheet/r/7QzTmWbaXLJnoPEd-kRyUgFhHsstbvCe2qfoMxDa_pz/view?mode=shared

Please feel free to design the business cards however you feel best. I am happy to give some creative freedoms and then provide feedback from there.

Please then also create a letterhead to match the business card design

Colors

Designer to choose colors to be used in the design.

Requirements
Must have
• Must be a modern, elegant business card which looks very professional

```html
<!DOCTYPE html>
<html lang="en">
<head>
<meta charset="utf-8">
<title>Pimlu – Business Card and Letterhead</title>
<link href="https://fonts.googleapis.com/css2?family=Montserrat:wght@500;600;800&family=Open+Sans:wght@400&family=Great+Vibes&display=swap" rel="stylesheet">
<style>
  :root {
    --backdrop: #a5b6bb;
    --paper: #ffffff;
    --ink: #3a3a3a;
    --muted: #555555;
    --brand-red: #e3161f;
    --card-dark: #2c2c2e;
    --card-back: #2f2f30;
    --back-name: #4a4a4c;
    --rule: #8c8c8c;
    --photo-a: #3b3b3d;
    --photo-b: #1f1f21;
  }
  * { box-sizing: border-box; margin: 0; padding: 0; }
  html, body { width: 1200px; height: 900px; overflow: hidden; }
  body { background: var(--backdrop); position: relative; font-family: "Open Sans", sans-serif; }

  .letterhead {
    position: absolute; left: 109px; top: 86px; width: 570px; height: 727px;
    background: var(--paper);
  }
  .letterhead__brand {
    position: absolute; top: 12px; left: 0; width: 100%; text-align: center;
    font-family: "Montserrat", sans-serif; font-weight: 800; font-size: 31px;
    letter-spacing: 1px; color: var(--brand-red);
  }
  .letter__date {
    position: absolute; left: 63px; top: 202px; font-size: 9.5px; color: var(--ink);
  }
  .letter__body {
    position: absolute; left: 63px; top: 246px; width: 450px;
    font-size: 9.2px; line-height: 21px; color: var(--ink);
  }
  .letter__body p + p { margin-top: 3px; }
  .letter__signoff { position: absolute; left: 397px; top: 510px; color: var(--ink); }
  .signoff__script { font-family: "Great Vibes", cursive; font-size: 21px; line-height: 1; margin-left: -6px; }
  .signoff__name, .signoff__role { font-size: 9px; line-height: 11px; }

  .letter__footer { position: absolute; left: 44px; top: 677px; width: 482px; text-align: center; }
  .footer__rule { position: absolute; top: 7px; left: 0; width: 100%; height: 1px; background: var(--rule); }
  .footer__icons { position: relative; display: inline-flex; gap: 2px; background: var(--paper); padding: 0 2px; }
  .footer__contact { font-size: 9.2px; color: #222; line-height: 14px; margin-top: 3px; }
  .footer__contact span + span { margin-left: 9px; }

  .icon-dot {
    width: 12px; height: 12px; border-radius: 50%; background: var(--brand-red);
    display: inline-flex; align-items: center; justify-content: center;
  }

  .card {
    position: absolute; left: 711px; width: 380px; height: 217px; overflow: hidden;
  }
  .card--front { top: 346px; background: var(--card-dark); border-bottom: 2px solid var(--brand-red); }
  .card--back { top: 597px; background: var(--card-back); border-bottom: 2px solid var(--brand-red); }

  .card__brand {
    position: absolute; left: 28px; top: 14px;
    font-family: "Montserrat", sans-serif; font-weight: 800; font-size: 37px;
    letter-spacing: 1px; color: var(--brand-red);
  }
  .card__name {
    position: absolute; left: 28px; top: 77px;
    font-family: "Montserrat", sans-serif; font-weight: 600; font-size: 13.5px;
    letter-spacing: 1px; color: var(--brand-red);
  }
  .card__title {
    position: absolute; left: 28px; top: 94px;
    font-family: "Montserrat", sans-serif; font-weight: 500; font-size: 10.5px; color: #fff;
  }
  .card__rule { position: absolute; left: 28px; height: 1px; width: 48px; background: var(--brand-red); }
  .card__rule--top { top: 112px; }
  .card__rule--bottom { top: 162px; }
  .card__contacts {
    position: absolute; left: 28px; top: 118px; list-style: none;
    font-family: "Montserrat", sans-serif; font-weight: 500; font-size: 10.5px; color: #fff; line-height: 13px;
  }
  .card__contacts li { display: flex; align-items: center; gap: 5px; }
  .card__contacts svg { width: 8px; height: 8px; flex: none; }
  .card__address {
    position: absolute; left: 28px; top: 166px;
    font-family: "Montserrat", sans-serif; font-weight: 500; font-size: 10.5px; color: #fff; line-height: 13px;
  }
  .card__portrait {
    position: absolute; right: 0; top: 0; width: 190px; height: 100%;
    background: linear-gradient(180deg, var(--photo-a), var(--photo-b));
  }
  .card__back-brand {
    position: absolute; left: 0; top: 78px; width: 100%; text-align: center;
    font-family: "Montserrat", sans-serif; font-weight: 800; font-size: 46px;
    letter-spacing: 2px; color: var(--back-name);
  }
</style>
</head>
<body>

<article class="letterhead">
  <div class="letterhead__brand">PIMLU</div>

  <p class="letter__date">Date, 10 September, 2020</p>

  <div class="letter__body">
    <p>This is a sample letter that has been placed to demonstrate typing format (Your Company). letterhead<br>design. When positioned properly, it will serve to work in harmony with all other elements letterhead.<br>This letterhead design is meant to project an image</p>
    <p>This letterhead design is meant project an image of professionalism reliability. By using simple align<br>we have created a very spacious feeling. The simplicity suggest strength the spaciousness contributes<br>aesthetics the layout. These basic qualities along with the (Your Company)</p>
    <p>look and helps reinforce the (Your Company) brand. letterhead design is meant to project an image<br>design. When positioned properly, it will serve to work in harmony all the other elements letterhead.<br>sionalism and reliability.</p>
    <p>This letterhead design is based on the (Form of your logo) form (Your Company) logo. Each stationery<br>we have created a very spacious feeling. The simplicity suggests strength the spaciousness contribute<br>part of the (Form of your logo).</p>
  </div>

  <div class="letter__signoff">
    <div class="signoff__script">Martin Calloway</div>
    <div class="signoff__name">Martin Calloway</div>
    <div class="signoff__role">Manager</div>
  </div>

  <footer class="letter__footer">
    <div class="footer__rule"></div>
    <div class="footer__icons">
      <span class="icon-dot"><svg width="7" height="7" viewBox="0 0 10 10"><path d="M2 1l2 2-1 1.2c.6 1.3 1.5 2.2 2.8 2.8L7 6l2 2-1.3 1.3C4.5 9 1 5.5.7 2.3z" fill="#fff"/></svg></span>
      <span class="icon-dot"><svg width="7" height="6" viewBox="0 0 10 8"><rect x=".5" y=".5" width="9" height="7" fill="none" stroke="#fff"/><path d="M.5.5l4.5 4 4.5-4" fill="none" stroke="#fff"/></svg></span>
      <span class="icon-dot"><svg width="7" height="7" viewBox="0 0 10 10"><circle cx="5" cy="5" r="4.3" fill="none" stroke="#fff"/><path d="M.7 5h8.6M5 .7c-2.4 2.6-2.4 6 0 8.6M5 .7c2.4 2.6 2.4 6 0 8.6" fill="none" stroke="#fff" stroke-width=".8"/></svg></span>
    </div>
    <div class="footer__contact">
      <span>0400 318 552</span><span>rowan@pimlu.com</span><span>www.pimlu.com</span><br>
      PO Box 7310, Calder Vale NSW 2690
    </div>
  </footer>
</article>

<section class="card card--front">
  <div class="card__brand">PIMLU</div>
  <div class="card__name">ROWAN ELLERY</div>
  <div class="card__title">Licenced Real Estate Agent</div>
  <div class="card__rule card__rule--top"></div>
  <ul class="card__contacts">
    <li><svg viewBox="0 0 10 10"><path d="M2 1l2 2-1 1.2c.6 1.3 1.5 2.2 2.8 2.8L7 6l2 2-1.3 1.3C4.5 9 1 5.5.7 2.3z" fill="var(--brand-red)"/></svg>0400 318 552</li>
    <li><svg viewBox="0 0 10 10"><rect x="0" y="1.5" width="10" height="7" rx="1" fill="var(--brand-red)"/><path d="M.5 2l4.5 3.5L9.5 2" fill="none" stroke="var(--card-dark)"/></svg>rowan@pimlu.com</li>
    <li><svg viewBox="0 0 10 10"><circle cx="5" cy="5" r="5" fill="var(--brand-red)"/><path d="M0 5h10M5 0c-2.4 2.6-2.4 7.4 0 10M5 0c2.4 2.6 2.4 7.4 0 10" fill="none" stroke="var(--card-dark)" stroke-width=".8"/></svg>www.pimlu.com</li>
  </ul>
  <div class="card__rule card__rule--bottom"></div>
  <div class="card__address">PO Box 7310<br>Calder Vale NSW 2690</div>
  <div class="card__portrait" role="img" aria-label="Portrait photograph of the agent in a dark suit"></div>
</section>

<section class="card card--back">
  <div class="card__back-brand">PIMLU</div>
</section>

</body>
</html>
```